Business Card Design Project

After recently finishing a design project for the company logo using markbazaar, it's now time for a business card. Attached to this is the logo.

The requirements for the business card are pretty straightforward:

- A clean, uncomplicated look
- Consistent usage of fonts
- Designs for both single sided and double sided cards
- A modern layout with preferably space to refer to social media accounts and/or downloadable vcards through a qr code
- consistent application of the company colour scheme: red/white. Hex codes for exact colour can be provided

Thanks!

```html
<!DOCTYPE html>
<html lang="en">
<head>
<meta charset="utf-8">
<title>Ember Lane Staffing – Business Card</title>
<link rel="stylesheet" href="https://fonts.googleapis.com/css2?family=Open+Sans:wght@400;600;700&display=swap">
<style>
  :root {
    --brand-red: #e3202a;
    --ink: #231f20;
    --ink-soft: #3a3a3a;
    --swoosh-grey: #9a9a9a;
    --divider: #b5b5b5;
    --card: #ffffff;
    --backdrop: #e9e7e4;
  }
  html, body {
    margin: 0;
    padding: 0;
    width: 960px;
    height: 1200px;
    overflow: hidden;
    background: var(--backdrop);
    font-family: "Open Sans", Arial, sans-serif;
    color: var(--ink);
  }
  .canvas {
    position: relative;
    width: 960px;
    height: 1200px;
  }
  .card {
    position: absolute;
    background: var(--card);
    border-radius: 30px;
    overflow: hidden;
  }
  .card--front { left: 62px; top: 83px; width: 838px; height: 479px; }
  .card--back  { left: 60px; top: 638px; width: 840px; height: 479px; }

  .swoosh { position: absolute; inset: 0; width: 100%; height: 100%; }

  .brand {
    position: absolute;
    display: flex;
    align-items: center;
  }
  .brand__mark {
    background: var(--brand-red);
    flex: none;
  }
  .brand__name {
    font-weight: 600;
    color: var(--ink);
    line-height: 1.02;
    letter-spacing: -0.5px;
  }
  .card--front .brand { left: 48px; top: 172px; gap: 22px; }
  .card--front .brand__mark { width: 78px; height: 78px; }
  .card--front .brand__name { font-size: 50px; }

  .card--back .brand { left: 140px; top: 150px; gap: 30px; }
  .card--back .brand__mark { width: 112px; height: 112px; }
  .card--back .brand__name { font-size: 70px; }

  .divider {
    position: absolute;
    left: 537px;
    top: 142px;
    width: 2px;
    height: 190px;
    background: var(--divider);
  }
  .contact {
    position: absolute;
    left: 563px;
    top: 164px;
    color: var(--ink-soft);
    font-size: 20px;
    line-height: 1.4;
  }
  .contact__name { font-size: 25px; font-weight: 700; color: var(--ink-soft); margin: 0; line-height: 1.3; }
  .contact__role { margin: 0 0 8px; }
  .contact__line { margin: 0; }
  .contact__line--gap { margin-top: 14px; }
  .contact__label { font-weight: 700; font-style: italic; color: var(--ink); }

  .address {
    position: absolute;
    left: 0;
    right: 0;
    top: 426px;
    text-align: center;
    font-size: 23px;
    color: var(--ink);
    margin: 0;
  }
</style>
</head>
<body>
<main class="canvas">

  <section class="card card--front" aria-label="Business card front">
    <svg class="swoosh" viewBox="0 0 838 479" aria-hidden="true">
      <path d="M690 0 Q800 6 838 44 L838 0 Z" fill="var(--brand-red)"/>
      <path d="M705 9 Q805 18 838 62 L838 46 Q795 14 705 9 Z" fill="var(--swoosh-grey)"/>
      <path d="M0 422 Q55 455 150 470 Q60 462 0 440 Z" fill="var(--swoosh-grey)"/>
      <path d="M0 444 Q60 468 150 479 L0 479 Z" fill="var(--brand-red)"/>
    </svg>

    <div class="brand">
      <span class="brand__mark"></span>
      <span class="brand__name">Ember Lane<br>Staffing</span>
    </div>

    <div class="divider"></div>

    <div class="contact">
      <p class="contact__name">Your Name</p>
      <p class="contact__role">Designation</p>
      <p class="contact__line"><span class="contact__label">t</span> : 123-123-1234</p>
      <p class="contact__line contact__line--gap"><span class="contact__label">e</span> : info@yourwebsite.com</p>
      <p class="contact__line"><span class="contact__label">w</span> : www.emberlane.com</p>
    </div>

    <p class="address">1234, Street Name, District, City, Country Code.</p>
  </section>

  <section class="card card--back" aria-label="Business card back">
    <div class="brand">
      <span class="brand__mark"></span>
      <span class="brand__name">Ember Lane<br>Staffing</span>
    </div>
  </section>

</main>
</body>
</html>
```